Four in One (Flexible infographic for Content Management Industry)

See attachment.
A graphic depicting 4 products, where each can stand on its own and each can be combined with others, but where, if all are taken together, the best result is achieved (the "super product").
Intended use is web. See attached file as an example.
The most basic idea is as the attached diagram shows, where 4 rectangles are arranged in a quadrangle, with a middle rectangle in the center representing the combined 4 products. This concept is fine except it is a bit too obvious as it stands. We are looking for either a variation of this or another concept.
The audience is technical + professional + enterprise - NOT consumers. Hence the design should be conservative in nature.
We are aware of tools like as Canva or Pictogram where such graphics are available, but we are looking for something with a bit more imagination and flexibility.
This graphic should be targeted to web sites and be delivered with vector-based (SVG) graphics.

```html
<!DOCTYPE html>
<html lang="en">
<head>
<meta charset="utf-8">
<title>Four in One – Super Product</title>
<link rel="stylesheet" href="https://fonts.googleapis.com/css2?family=Montserrat:wght@600;700;800;900&family=Arimo:wght@500;600&display=swap">
<style>
  :root {
    --ink: #333132;
    --frame: #3a3a3a;
    --doc: #3d3f94;
    --sec: #66335a;
    --sec-icon: #b5197f;
    --erp: #c07d0c;
    --erp-icon: #ef8230;
    --dig: #56aab3;
    --ring: #e6e7e9;
    --paper: #ffffff;
  }
  html, body {
    margin: 0;
    padding: 0;
    width: 1153px;
    height: 1200px;
    overflow: hidden;
    background: var(--paper);
  }
  .canvas {
    position: relative;
    width: 1872px;
    height: 1950px;
    transform: scale(0.6159);
    transform-origin: 0 0;
    font-family: "Montserrat", sans-serif;
    color: var(--ink);
  }
  .diagram { position: absolute; inset: 0; }
  .block { position: absolute; }
  .title {
    font-weight: 700;
    margin: 0;
    letter-spacing: 0.5px;
  }
  .body-text { margin: 0; font-weight: 600; }
  .features {
    list-style: none;
    margin: 0;
    padding: 0;
    font-weight: 600;
  }
  .features li { position: relative; }
  .features li::before {
    content: "";
    position: absolute;
    width: 6px;
    height: 11px;
    border-right: 3px solid var(--ink);
    border-bottom: 3px solid var(--ink);
    transform: rotate(40deg);
  }
  .icon { position: absolute; }

  /* Document Management */
  .doc-title { left: 300px; top: 296px; width: 405px; text-align: right; font-size: 47px; line-height: 56px; }
  .doc-body { left: 298px; top: 508px; width: 600px; font-family: "Arimo", sans-serif; font-size: 24.5px; line-height: 34px; font-weight: 600; }
  .doc-list { left: 300px; top: 635px; font-family: "Arimo", sans-serif; font-size: 25px; line-height: 30px; }
  .doc-list li { padding-left: 28px; }
  .doc-list li::before { left: 3px; top: 8px; }

  /* Security and Compliance */
  .sec-title { left: 1158px; top: 290px; font-size: 43px; line-height: 50px; }
  .sec-body { left: 1010px; top: 498px; width: 560px; font-size: 20px; line-height: 25px; }
  .sec-list { left: 1197px; top: 645px; font-size: 20px; line-height: 25.6px; }
  .sec-list li { padding-left: 40px; }
  .sec-list li::before { left: 4px; top: 5px; }

  /* Enterprise Resource Planning */
  .erp-title { left: 300px; top: 1140px; width: 331px; text-align: right; font-size: 34px; line-height: 41px; white-space: nowrap; }
  .erp-title span { display: block; }
  .erp-body { left: 334px; top: 1328px; width: 540px; font-size: 20px; line-height: 25.6px; }
  .erp-list { left: 366px; top: 1452px; font-size: 20px; line-height: 25.6px; }
  .erp-list li { padding-left: 31px; }
  .erp-list li::before { left: 4px; top: 5px; }

  /* Digital Transformation */
  .dig-title { left: 1267px; top: 1140px; font-size: 36px; line-height: 45px; }
  .dig-body { left: 1044px; top: 1328px; width: 540px; font-size: 20px; line-height: 25.6px; }
  .dig-list { left: 1052px; top: 1452px; font-size: 20px; line-height: 25.6px; }
  .dig-list li { padding-left: 39px; }
  .dig-list li::before { left: 4px; top: 5px; }

  /* Centre */
  .hub-title {
    left: 636px; top: 872px; width: 580px;
    text-align: center;
    font-weight: 900;
    font-size: 90px;
    line-height: 80px;
    letter-spacing: -1px;
    margin: 0;
  }
  .hub-title span { display: block; }
</style>
</head>
<body>
<main class="canvas">
  <svg class="diagram" width="1872" height="1950" viewBox="0 0 1872 1950" aria-hidden="true">
    <rect class="frame" x="2" y="16" width="1867" height="1931" fill="none" stroke="var(--frame)" stroke-width="2"/>
    <g fill="none" stroke-width="10">
      <path class="card-doc" stroke="var(--doc)" d="M590 230 H820 A80 80 0 0 1 900 310 V953 H330 A65 65 0 0 1 265 888 V555 A325 325 0 0 1 590 230 Z"/>
      <path class="card-sec" stroke="var(--sec)" d="M970 310 A80 80 0 0 1 1050 230 H1285 A322 322 0 0 1 1607 552 V888 A65 65 0 0 1 1542 953 H970 Z"/>
      <path class="card-erp" stroke="var(--erp)" d="M265 1073 A65 65 0 0 1 330 1008 H900 V1653 A80 80 0 0 1 820 1733 H590 A325 325 0 0 1 265 1408 Z"/>
      <path class="card-dig" stroke="var(--dig)" d="M970 1008 H1542 A65 65 0 0 1 1607 1073 V1408 A325 325 0 0 1 1282 1733 H1050 A80 80 0 0 1 970 1653 Z"/>
    </g>
    <circle class="hub-ring" cx="936" cy="983" r="285" fill="var(--paper)" stroke="var(--ring)" stroke-width="74"/>
    <g class="dividers" stroke="var(--ink)" stroke-width="3">
      <line x1="352" y1="471" x2="840" y2="471"/>
      <line x1="1040" y1="471" x2="1528" y2="471"/>
      <line x1="352" y1="1284" x2="752" y2="1284"/>
      <line x1="1116" y1="1284" x2="1528" y2="1284"/>
    </g>
    <!-- document icon -->
    <g class="icon-doc" fill="none" stroke="var(--doc)" stroke-width="3.5" stroke-linejoin="round">
      <path d="M745 307 H788 L802 321 V385 H745 Z"/>
      <path d="M788 307 V321 H802"/>
      <path d="M754 329 H793 M754 339 H793 M754 349 H793 M754 359 H793"/>
    </g>
    <!-- shield icon -->
    <g class="icon-shield" fill="none" stroke="var(--sec-icon)" stroke-width="6" stroke-linejoin="round">
      <path d="M1089 298 C1098 308 1112 312 1125 311 V345 C1125 365 1110 378 1089 385 C1068 378 1053 365 1053 345 V311 C1066 312 1080 308 1089 298 Z"/>
      <path d="M1073 340 L1086 352 L1105 329" stroke-width="8" stroke-linecap="round"/>
    </g>
    <!-- pages icon -->
    <g class="icon-pages" fill="none" stroke="var(--erp-icon)" stroke-width="4" stroke-linejoin="round">
      <path d="M335 1090 H396 V1160 H335 Z"/>
      <path d="M324 1078 H384 V1150 H324 Z" fill="var(--paper)"/>
      <path d="M334 1096 H374 M334 1108 H374 M334 1120 H374 M334 1132 H374"/>
    </g>
    <!-- wireless icon -->
    <g class="icon-wifi" fill="none" stroke="var(--dig)" stroke-width="12" stroke-linecap="round">
      <path d="M1460 1110 A62 62 0 0 1 1542 1110"/>
      <path d="M1474 1127 A40 40 0 0 1 1528 1127"/>
      <circle cx="1501" cy="1150" r="7" fill="var(--dig)" stroke-width="5"/>
    </g>
  </svg>

  <h2 class="block title doc-title">Document<br>Management</h2>
  <p class="block body-text doc-body">Streamline document organization, access, and collaboration with easier file storage and sharing, leading to more efficient workflows .</p>
  <ul class="block features doc-list">
    <li>Centralized Document Control</li>
    <li>Collaborative Workspace Integration</li>
    <li>Automated Compliance Tracking</li>
    <li>Check 4</li>
  </ul>

  <h2 class="block title sec-title">Security<br>and Compliance</h2>
  <p class="block body-text sec-body">Benefit from tailored cloud solutions, secure data storage, and expert disaster recovery planning for reliable and scalable IT operations.</p>
  <ul class="block features sec-list">
    <li>Custom Cloud Solutions</li>
    <li>Secure Data Storage</li>
    <li>Expert Disaster Recovery</li>
    <li>Check 4</li>
  </ul>

  <h2 class="block title erp-title"><span>Enterprise</span><span>Resource Planning</span></h2>
  <p class="block body-text erp-body">Simplify management across finance, sales, and operations, enabling better decision-making and improved productivity.</p>
  <ul class="block features erp-list">
    <li>Integrated Business Processes</li>
    <li>Enhanced Decision-Making</li>
    <li>Productivity Improvement</li>
    <li>Check 4</li>
  </ul>

  <h2 class="block title dig-title">Digital<br>Transformation</h2>
  <p class="block body-text dig-body">Turn scanned documents into easily searchable digital archives, boosting efficiency and accessibility.</p>
  <ul class="block features dig-list">
    <li>Instant searchable Archives with OCR</li>
    <li>Automated Document Classification</li>
    <li>DocuHub and Cloud Blob Ready</li>
    <li>Check 4</li>
  </ul>

  <h1 class="block hub-title"><span>Super</span><span>Product</span></h1>
</main>
</body>
</html>
```